Velmora Gems - High end custom Jewelry website

I need a web design for an online custom jewelry company called Velmora Gems. (www.velmoragems-demo.com) this company specializes in high-end custom made engagement rings, wedding bands and jewelry of all kinds (necklaces, earrings, bracelets etc)All our jewelry uses diamonds so there must be a focus on diamonds on every type of jewelry we will be designing off the website.

We are a company located in New York City but our website will
aim to cater to international, national clients and as well as New York city residents.The company low overhead provides diamonds and precious metal at a discounted costs compared to its competitors. Velmora Gems makes unique custom diamond jewelry of a higher quality and at a lower price than carriage trade retail jewellers. (meaning that our company allows our customers to save money on diamond jewelry then they would if they bought from any known store or company)

The website will act as a tool for our customers to create their own jewelry. The way they will do this is by uploading pictures of what they like, they can post any pictures they want (from drawings, to actual copy and pasted pictures from other websites of designs) From these designs we will create a 3D digital image of the jewelry they like and customize it - however they want (colours, size etc) and then give them a quote in price. From the quote they will either approve it and we can have it made for them in 1 weeks time. If they decline it we will try to do whatever it is they want for the design to suit their needs.

We want the website to be simple and user friendly since people will be working on it to create their own individual jewelry pieces. Therefore some useful headings should include:

"Custom Jewellery" or something like "your design" "Custom Design"

a drop heading here should show the following steps into creating the jewelry.

step 1:
upload pictures of the designs you like
step 2:
What is your ring size?
Step 3:
What setting would you like your ring in? platinum, 14k etc..
Step 4:
What is your budget?
Step 5 :
Once you’ve uploaded pictures and give an explanation of what you want then we will contact you by phone or email and proceed to design your ring. Give us your contact info in this step.

Other then that other headings id like to see on the site are:

"Home"
main page with appealing picture which I can later add text to it explaining our company

"About us"
will include a brief section of who we are

"Wedding/engagment"

We are based in New York City and our company offers a one-to-one personal service to our clients ensuring their expectations are well met and, if we can help it, surpassed. We are a personal shopping and diamond supplier to individuals. Custom design is our speciality weather it be wedding ring, engagement ring or anniversary ring we aim to create distinctive designs that both reflect your personality as well as the beauty of the gemstones used in your piece. We use platinum, 14l-18k gold and diamonds to whatever it is that you may desire.
We in our company believe that we are privileged to be a part of one of the biggest events in our customer’s lives, and we pride ourselves on making sure that our customers have the best experience possible. As the diamond is the center piece of every engagement ring, we at VG make sure that our clients find the best diamond possible that is within their budget. Similarly, we work with established jewellery artisans from Belgium to provide the highest possible craftsmanship to a ring design of your choice. We make sure that our rings are made by the true and tried traditional methods focused on quality rather than quantity and of course our diamonds are QRB certified.

Diamonds

A section that explains where our diamonds come from. A heading will drop down here that is a diamond guide, as shown below.
Diamond Guide

An overview of the 4 C’s and different settings, a section for a brief education on diamonds.
Client Experiences

A section where clients share their experiences with Velmora Gems and can post pictures and share stories about their engagement etc.

The colour i would like to see are white and black, white and dark blue or royal blue. I don't think pastel colours will look good with this, maybe accents of purple or something pastel but for the main colours I want to keep it classic and sophisticated since it is a diamond company.

"Sign in | Check out"
where users are able to create a profile and upload their pictures and create their designs..

and a "search section"

or something along these lines or if you can incorporate both:

Exquisite craftsmanship Finest quality diamonds
Will beat any competitors price by twenty to seventy percent guaranteed
Price quotes whitin24 hours

Upload design picture or sketch
Receive price quote within 24hours
Receive and approve free customized design
Receive you jewelry in 1 week or less

Engagment Ring or necklace, earring, etc
Name
EMail
phone
Competitior Link
Budget

The final design should communicate that Velmora Gems is a custom jewelry site that allows individuals to personalize any type of jewellery they want with diamonds - at a fraction of the cost in comparison to any other out there. Our team works very hard to ensure that you will be so involved in the custom order process that there is no chance of something not being made to your requests. Jewelry is made to the highest standard or it does not ship in the first place. In the event a custom order does not suit a customer, we will take returns within 14 days of delivery less a 25% restocking fee.

Target Market(s)

middle class and upper class people ages 25-45

Industry/Entity Type

Digital

Requirements
Must have
• We have the logo now that I will attach BUT if you want to design something else please feel free ! I am open to all designs and ideas.
My logo now is simply a sketch so even if we make it look a bit more professional and classy I would like that, I think I want to keep it simple just black and white and maybe make the diamond shiny if possible. other then black in white I liked the gold and black combination too.. but as I said open to any other creative ideas!

can take pictures of jewelry off this website:
http://www.plinthwaredesigns.example/library/rings.html
Nice to have
• We already have a logo but we would like to see a banner or something that indicated saving money on diamond jewelry without it looking tacky or too cheap..

Also would like to see artistic pictures if you can of jewelry alongside very simple designs of jewelry that the masses like, (anything trendy or appealing to the eye)

cursive or elegant writing could be nice, flash could also be incorporated in the main page..

Should not have
• Nothing to old fashioned, when I mean elegant maybe just the the name of the company in cursive writing (Velmora Gems) but the actual headings and font on the website to be in a widely used font on jewelry websites. Please no hot pink colours or anything neon..
no times new roman font..

```html
<!DOCTYPE html>
<html lang="en">
<head>
<meta charset="utf-8">
<title>Velmora Gems – Custom Diamond Jewellery</title>
<link rel="stylesheet" href="https://fonts.googleapis.com/css2?family=PT+Sans:wght@400;700&family=PT+Sans+Narrow:wght@400;700&family=Oswald:wght@500;600&display=swap">
<style>
:root{
  --black:#000;
  --ink:#333;
  --grey-text:#555;
  --soft-grey:#ebebeb;
  --panel-grey:#d4d4d4;
  --field:#f1f1f1;
  --page:#f0f0f0;
  --royal:#0b2d66;
  --dot-blue:#3b7fd0;
  --white:#fff;
}
*{margin:0;padding:0;box-sizing:border-box}
html,body{width:1200px;height:1158px;overflow:hidden}
body{position:relative;background:var(--white);font-family:"PT Sans",sans-serif;color:var(--ink)}
.abs{position:absolute}

.topbar{left:0;top:0;width:1200px;height:50px;background:var(--black)}
.search-field{left:744px;top:13px;width:154px;height:23px;background:#222;border:1px solid #333;border-radius:2px 0 0 2px}
.search-btn{left:898px;top:13px;width:46px;height:23px;background:#444;color:#ddd;font-size:8px;line-height:23px;text-align:center;letter-spacing:.3px}
.login{left:979px;top:16px;color:var(--white);font-size:13px}

.page-band{left:0;top:50px;width:1200px;height:818px;background:var(--page)}

.brand{left:124px;top:88px;display:flex;align-items:center;gap:10px}
.brand-dot{width:18px;height:18px;border-radius:50%;background:var(--black)}
.brand-name{font-family:"PT Sans",sans-serif;font-size:22px;font-weight:400;color:var(--black);letter-spacing:1px}

.bag{left:962px;top:90px;width:40px;height:55px;background:linear-gradient(160deg,#fafafa,#bdbdbd);border-radius:2px}
.bag-label{left:892px;top:150px;font-size:12px;color:var(--grey-text);letter-spacing:-.3px}

.nav{left:120px;top:174px;width:961px;height:53px;background:var(--black)}
.nav ul{list-style:none;display:flex;position:absolute;left:23px;top:16px;gap:23px}
.nav li{color:var(--white);font-size:17px}
.quick-btn{left:904px;top:186px;width:150px;height:27px;background:var(--royal);color:var(--white);font-weight:700;font-size:14px;line-height:27px;padding-left:19px}
.quick-btn svg{position:absolute;right:16px;top:10px}

.hero{left:121px;top:232px;width:960px;height:388px;background:var(--black);overflow:hidden}
.hero-ring{left:135px;top:33px;width:250px;height:355px;background:radial-gradient(ellipse at 45% 40%,#e6e6e6 0%,#9a9a9a 45%,#1a1a1a 80%);border-radius:40% 40% 10% 10%}
.hero-title{left:476px;top:78px;font-family:"Oswald",sans-serif;font-weight:600;font-size:54px;color:var(--white);white-space:nowrap;letter-spacing:-.5px}
.hero-sub{left:616px;top:157px;font-family:"PT Sans Narrow",sans-serif;font-size:22px;color:var(--white);white-space:nowrap}
.hero-cta{left:666px;top:208px;width:140px;height:56px;background:var(--royal)}
.dots{left:442px;top:349px;display:flex;gap:8px}
.dots span{width:13px;height:13px;border-radius:50%;background:var(--white)}
.dots span.on{background:var(--dot-blue)}

.quick-panel{left:798px;top:214px;width:256px;height:314px;background:var(--panel-grey)}
.quick-panel h2{position:absolute;left:12px;top:22px;color:var(--royal);font-size:19px;font-weight:700}
.field{position:absolute;left:15px;width:228px;height:33px;background:var(--field);font-family:"PT Sans Narrow",sans-serif;font-size:12px;color:#777;line-height:33px;padding-left:12px}
.field svg{position:absolute;right:10px;top:12px}
.submit{position:absolute;left:64px;top:264px;width:132px;height:32px;background:var(--royal);color:var(--white);font-weight:700;font-size:18px;text-align:center;line-height:32px;border-bottom:2px solid #06214d}

.card{top:638px;width:300px;height:189px;background:var(--soft-grey)}
.card h3{position:absolute;left:18px;top:44px;font-size:28px;font-weight:400;color:#3d3d3d;line-height:36px}
.card h3 span{display:block;font-family:"PT Sans Narrow",sans-serif;font-size:30px}
.buy{position:absolute;left:18px;top:124px;width:84px;height:26px;background:var(--black);color:var(--white);font-size:11px;line-height:26px;padding-left:11px}
.card-img{position:absolute;background:radial-gradient(ellipse,#f6f6f6 0%,#c9c9c9 55%,rgba(235,235,235,0) 75%)}

.foot-col{top:887px;list-style:none;font-size:11px;color:var(--grey-text);line-height:22.5px}
.foot-col.mid{line-height:23.5px}
.social{left:934px;top:887px;width:126px;font-size:11px;color:var(--grey-text)}
.social li{list-style:none;position:absolute;left:0;width:126px}
.social .circ{position:absolute;right:1px;width:27px;height:27px;border-radius:50%;background:#111}

.tagline{top:1040px;font-family:"PT Sans Narrow",sans-serif;font-size:17px;color:var(--ink);white-space:nowrap}
.vsep{top:1030px;width:1px;height:41px;background:#ddd}
.hline{left:0;top:1089px;width:1200px;height:1px;background:#ddd}
.copyright{left:0;top:1113px;width:1100px;text-align:center;font-size:11px;color:var(--grey-text)}
</style>
</head>
<body>

<header>
  <div class="abs topbar"></div>
  <div class="abs search-field"></div>
  <div class="abs search-btn">SEARCH</div>
  <div class="abs login">LOGIN</div>
</header>

<div class="abs page-band"></div>

<div class="abs brand"><span class="brand-dot"></span><span class="brand-name">Velmora Gems</span></div>

<div class="abs bag" role="img" aria-label="Shopping bag icon"></div>
<div class="abs bag-label">Shopping Bag Selected (0)</div>

<nav class="abs nav">
  <ul>
    <li>Home</li><li>About Us</li><li>Custom Jewllery</li><li>Collections</li><li>Contact Us</li>
  </ul>
</nav>

<section class="abs hero">
  <div class="abs hero-ring" role="img" aria-label="Photograph of a platinum solitaire diamond engagement ring"></div>
  <div class="abs hero-title">WE DO CUSTOM DESIGNS</div>
  <div class="abs hero-sub">NECKLACES, EARRINGS &amp; RINGS</div>
  <div class="abs hero-cta"></div>
  <div class="abs dots"><span></span><span></span><span></span><span class="on"></span></div>
</section>

<div class="abs quick-btn">Quick Contact
  <svg width="9" height="7" viewBox="0 0 9 7"><path d="M0 0h9L4.5 7z" fill="#3b7fd0"/></svg>
</div>

<form class="abs quick-panel">
  <h2>Engagement Ring</h2>
  <div class="field" style="top:57px">Name</div>
  <div class="field" style="top:99px">E-Mail</div>
  <div class="field" style="top:141px">Phone</div>
  <div class="field" style="top:183px">Competitor Link</div>
  <div class="field" style="top:225px">Budget
    <svg width="10" height="8" viewBox="0 0 10 8"><path d="M0 0h10L5 8z" fill="#222"/></svg>
  </div>
  <div class="submit">SUBMIT</div>
</form>

<section>
  <article class="abs card" style="left:128px">
    <h3>Necklace<span>Collections</span></h3>
    <div class="buy">BUY NOW</div>
    <div class="card-img" style="left:154px;top:30px;width:100px;height:117px" role="img" aria-label="Photograph of a diamond necklace"></div>
  </article>
  <article class="abs card" style="left:448px">
    <h3 style="left:16px">Earring<span>Collections</span></h3>
    <div class="buy">BUY NOW</div>
    <div class="card-img" style="left:147px;top:47px;width:120px;height:100px" role="img" aria-label="Photograph of diamond flower stud earrings"></div>
  </article>
  <article class="abs card" style="left:769px">
    <h3 style="left:16px">Bracelet<span>Collections</span></h3>
    <div class="buy">BUY NOW</div>
    <div class="card-img" style="left:136px;top:30px;width:110px;height:117px" role="img" aria-label="Photograph of a diamond link bracelet"></div>
  </article>
</section>

<footer>
  <ul class="abs foot-col" style="left:128px"><li>Home</li><li>About Us</li><li>Custom Jewllery</li><li>Collections</li><li>Contact Us</li></ul>
  <ul class="abs foot-col mid" style="left:369px"><li>Contact Us</li><li>Customer Services</li><li>Terms &amp; Conditions</li><li>Privacy Policy</li></ul>
  <ul class="abs foot-col mid" style="left:609px"><li>Delivery &amp; Returns’</li><li>Returns Policy</li><li>Store Locator</li><li>Gift Card</li><li>Custom Jewellery</li></ul>
  <ul class="abs social">
    <li style="top:0">Circlefeed<span class="circ" style="top:-2px"></span></li>
    <li style="top:47px">Chirpline<span class="circ" style="top:-14px"></span></li>
    <li style="top:94px">Workgrid<span class="circ" style="top:-15px"></span></li>
  </ul>

  <div class="abs tagline" style="left:130px">Exquisite craftsmanship a finest quality diamonds</div>
  <div class="abs vsep" style="left:423px"></div>
  <div class="abs tagline" style="left:440px">Will beat any competitors price by twenty to seventy percent guaranteed</div>
  <div class="abs vsep" style="left:867px"></div>
  <div class="abs tagline" style="left:890px">Price quotes within 24 hours</div>

  <div class="abs hline"></div>
  <div class="abs copyright">©2013 Company Name , All Rights Reserved &nbsp;| &nbsp;Privacy Policy &nbsp; | &nbsp;Terms &amp; Conditions</div>
</footer>

</body>
</html>
```